Redesign of business card for Cedar Ridge Mechanical

We are looking for a new design for our business cards for Cedar Ridge Mechanical. We are a plumbing & HVAC construction company, operating on the West Coast of Canada and USA. Logo attached.
Industry/Entity Type
Construction - Plumbing & HVAC
Contact Information for Business Card
Name, address, phone numbers, email, website address
Look and feel
Each slider illustrates characteristics of the customer's brand and the style your logo design should communicate.

```html
<!DOCTYPE html>
<html lang="en">
<head>
<meta charset="UTF-8">
<title>Cedar Ridge Mechanical – Business Card</title>
<link rel="stylesheet" href="https://fonts.googleapis.com/css2?family=Poppins:wght@300;400;600;700&display=swap">
<style>
  :root {
    --page-bg: #d9dada;
    --card-dark: #222226;
    --card-light: #e8e9e9;
    --ink-light: #ffffff;
    --ink-soft: #dcdcdc;
    --ink-brand-back: #b9bbbb;
  }
  * { box-sizing: border-box; margin: 0; padding: 0; }
  html, body {
    width: 1200px; height: 780px; overflow: hidden;
    background: var(--page-bg);
    font-family: 'Poppins', sans-serif;
  }
  .stage {
    width: 1200px; height: 780px;
    display: flex; align-items: center; justify-content: center; gap: 44px;
  }
  .card {
    position: relative;
    width: 525px; height: 300px;
    box-shadow: 0 10px 26px rgba(0,0,0,0.22);
    overflow: hidden;
  }
  .card--front { background: var(--card-dark); color: var(--ink-light); }
  .card--back {
    background: var(--card-light);
    display: flex; align-items: center; justify-content: center;
  }

  .brand { position: absolute; left: 34px; top: 34px; display: flex; align-items: center; gap: 12px; }
  .brand__mark { width: 30px; height: 30px; border: 3px solid var(--ink-light); }
  .brand__name {
    font-weight: 600; font-size: 15px; letter-spacing: 1.5px; text-transform: uppercase;
  }

  .address {
    position: absolute; left: 34px; top: 150px;
    font-weight: 300; font-size: 14px; line-height: 1.45; color: var(--ink-soft);
  }
  .contacts {
    position: absolute; left: 34px; top: 205px; list-style: none;
    font-weight: 300; font-size: 14px; line-height: 1.55; color: var(--ink-soft);
  }
  .contacts li { display: flex; align-items: center; gap: 10px; }
  .contacts svg { width: 13px; height: 13px; fill: var(--ink-light); flex: none; }

  .person { position: absolute; right: 40px; top: 40px; text-align: right; }
  .person__name { font-size: 27px; line-height: 1.1; font-weight: 300; }
  .person__first { font-weight: 700; }
  .person__title { font-size: 13px; font-weight: 400; margin-top: 4px; letter-spacing: 0.5px; }
  .edge-bar {
    position: absolute; right: 0; top: 38px;
    width: 18px; height: 54px; background: var(--ink-light);
  }

  .back-brand { display: flex; align-items: center; gap: 16px; }
  .back-brand__mark { width: 44px; height: 44px; border: 4px solid var(--ink-brand-back); }
  .back-brand__name {
    font-weight: 600; font-size: 24px; letter-spacing: 2px; text-transform: uppercase;
    color: var(--ink-brand-back);
  }
</style>
</head>
<body>
<main class="stage">
  <section class="card card--front">
    <div class="brand">
      <span class="brand__mark"></span>
      <span class="brand__name">Cedar Ridge Mechanical</span>
    </div>

    <div class="person">
      <p class="person__name"><span class="person__first">Marta</span> Kovic</p>
      <p class="person__title">Founder &amp; CEO</p>
    </div>
    <span class="edge-bar"></span>

    <address class="address">
      1840 Harbor Ln. Suite 310<br>
      Tacoma, WA 98402
    </address>

    <ul class="contacts">
      <li>
        <svg viewBox="0 0 24 24" aria-hidden="true"><path d="M6.6 10.8a15.1 15.1 0 0 0 6.6 6.6l2.2-2.2a1 1 0 0 1 1-.25 11.4 11.4 0 0 0 3.6.57 1 1 0 0 1 1 1V20a1 1 0 0 1-1 1A17 17 0 0 1 3 4a1 1 0 0 1 1-1h3.5a1 1 0 0 1 1 1c0 1.25.2 2.45.57 3.6a1 1 0 0 1-.25 1z"/></svg>
        (253) 555-0147
      </li>
      <li>
        <svg viewBox="0 0 24 24" aria-hidden="true"><path d="M12 2a10 10 0 1 0 0 20 10 10 0 0 0 0-20zm6.9 6h-2.9a15.6 15.6 0 0 0-1.4-3.6A8 8 0 0 1 18.9 8zM12 4a14 14 0 0 1 1.9 4h-3.8A14 14 0 0 1 12 4zM4.3 14a8 8 0 0 1 0-4h3.4a16.5 16.5 0 0 0 0 4zm.8 2h2.9a15.6 15.6 0 0 0 1.4 3.6A8 8 0 0 1 5.1 16zM8 8H5.1a8 8 0 0 1 4.3-3.6A15.6 15.6 0 0 0 8 8zm4 12a14 14 0 0 1-1.9-4h3.8A14 14 0 0 1 12 20zm2.3-6H9.7a14.7 14.7 0 0 1 0-4h4.6a14.7 14.7 0 0 1 0 4zm.3 5.6a15.6 15.6 0 0 0 1.4-3.6h2.9a8 8 0 0 1-4.3 3.6zm1.7-5.6a16.5 16.5 0 0 0 0-4h3.4a8 8 0 0 1 0 4z"/></svg>
        info@cedarridgemech.com
      </li>
      <li>
        <svg viewBox="0 0 24 24" aria-hidden="true"><path d="M2 6a2 2 0 0 1 2-2h16a2 2 0 0 1 2 2v12a2 2 0 0 1-2 2H4a2 2 0 0 1-2-2zm2 .4V8l8 5 8-5V6.4l-8 5z"/></svg>
        www.cedarridgemech.com
      </li>
    </ul>
  </section>

  <section class="card card--back">
    <div class="back-brand">
      <span class="back-brand__mark"></span>
      <span class="back-brand__name">Cedar Ridge Mechanical</span>
    </div>
  </section>
</main>
</body>
</html>
```